I need a flyer made , the flyer can be one page or two pages or three pages . I will be posting this on Instagram and social media platforms. I am a luxury home builder , I am looking to hire a construction project manager . Below are some examples and ideas what can be on the flyer

We’re looking for a construction project manager who’s passionate about building luxury homes at the highest standards
We’re hiring construction project manager
* Experience 5+ years in residential project management with a strong portfolio of completed homes.
* location : Bergen County NJ
* excellent leadership skills, leads teams with confidence and clarity
* communicates seamlessly with architects , engineers, designers and clients
*knows how to manage budgets and timelines without compromising quality
*solves problems with a positive solution first mindset
* pays attention to every detail because in luxury the small things are the big things

Apply now , link in bio or DM to connect.

My logo is attached, my web site www.velstridebuilders.com
My style is modern but still warm and inviting. I like a clean classy look .

Please don’t add any images of chairs or people to the flyer , I do not want people on my flyer. Do not add standard images of offices and houses , we are luxury builders , we build homes over 2 million dollars. Keep a classy , simple modern look . High end .

You can add a white hard hat with my logo on it for a image , this is a suggestion does not have to be on my flyer ,

```html
<!DOCTYPE html>
<html lang="en">
<head>
<meta charset="utf-8">
<title>Hiring: Construction Project Manager</title>
<link href="https://fonts.googleapis.com/css2?family=Allura&family=Poppins:wght@300;400;500;600;700;800&display=swap" rel="stylesheet">
<style>
  :root {
    --stage: #6b6b6b;
    --paper: #ffffff;
    --paper-shade: #e4e4e4;
    --ink: #0a0a0a;
    --ink-soft: #444444;
    --panel-dark: #000000;
    --panel-mid: #3a3a3a;
    --panel-end: #1c1c1c;
    --white: #ffffff;
    --pin-red: #e3161b;
    --pin-dark: #a80d10;
    --outline: #555555;
  }
  * { box-sizing: border-box; margin: 0; padding: 0; }
  html, body { width: 1200px; height: 973px; overflow: hidden; }
  body { background: var(--stage); font-family: 'Poppins', sans-serif; color: var(--ink); position: relative; }

  .flyer {
    position: absolute; left: 0; top: 86px; width: 1200px; height: 800px; overflow: hidden;
    background:
      radial-gradient(ellipse 60% 40% at 30% 20%, var(--paper) 0%, transparent 70%),
      radial-gradient(ellipse 50% 60% at 75% 55%, #f3f3f3 0%, transparent 70%),
      linear-gradient(160deg, #f7f7f7 0%, var(--paper-shade) 45%, #f9f9f9 70%, #e9e9e9 100%);
  }

  .sketch-area {
    position: absolute; left: 780px; top: 40px; width: 420px; height: 760px;
    background: linear-gradient(120deg, rgba(200,200,200,0) 0%, rgba(190,190,190,0.35) 60%, rgba(210,210,210,0.2) 100%);
  }
  .portrait-area {
    position: absolute; left: 790px; top: 62px; width: 330px; height: 700px; border-radius: 160px 160px 30px 30px;
    background: linear-gradient(180deg, #d9d3c4 0%, #3a3d4a 35%, #22242e 70%, #2a2a2a 100%);
  }
  .megaphone-area {
    position: absolute; left: 310px; top: 38px; width: 130px; height: 140px; border-radius: 40px;
    background: radial-gradient(circle at 60% 40%, #d8d8d8 0%, #8d8d8d 55%, rgba(120,120,120,0) 75%);
  }

  .script-lead {
    position: absolute; left: 60px; top: 58px; font-family: 'Allura', cursive; font-size: 112px;
    line-height: 1; color: #2b2b2b;
  }
  .headline {
    position: absolute; left: 58px; top: 160px; font-weight: 800; font-size: 138px; line-height: 1;
    letter-spacing: -5px; color: var(--ink);
  }
  .role { position: absolute; left: 62px; top: 310px; line-height: 1.02; }
  .role-top { font-size: 36px; font-weight: 700; color: var(--ink-soft); letter-spacing: 0.2px; }
  .role-bottom { font-size: 32px; font-weight: 300; color: var(--ink); }
  .role-bottom strong { font-weight: 700; }

  .tag {
    position: absolute; left: 384px; width: 166px; height: 32px; border-radius: 4px 16px 16px 4px;
    color: var(--white); font-size: 15px; font-weight: 400; padding-left: 12px; line-height: 32px;
  }
  .tag strong { font-weight: 700; }
  .tag-build { top: 316px; background: var(--ink); }
  .tag-lead { top: 354px; background: var(--ink-soft); }

  .requirements {
    position: absolute; left: 62px; top: 414px; width: 752px; height: 207px; border-radius: 22px; overflow: hidden;
    display: flex;
  }
  .req-col { padding: 26px 20px 0 32px; color: var(--white); }
  .req-col-left { width: 376px; background: var(--panel-dark); }
  .req-col-right { flex: 1; background: linear-gradient(90deg, var(--panel-mid) 0%, #2a2a2a 60%, var(--panel-end) 100%); padding-left: 16px; }
  .req-item { position: relative; padding-left: 18px; font-size: 14.3px; line-height: 17.5px; margin-bottom: 11px; font-weight: 400; }
  .req-item strong { font-weight: 600; }
  .req-item svg { position: absolute; left: 0; top: 4px; width: 11px; height: 11px; }

  .cta { position: absolute; top: 649px; height: 40px; border-radius: 20px; font-weight: 700; line-height: 38px; text-align: center; }
  .cta-apply { left: 62px; width: 162px; background: var(--ink); color: var(--white); font-size: 20px; }
  .cta-link { left: 222px; width: 328px; border: 1.5px solid var(--outline); background: var(--paper); color: #2b2b2b; font-size: 19px; font-weight: 600; }

  .contact { position: absolute; top: 698px; }
  .contact h3 { font-size: 20px; font-weight: 600; line-height: 26px; color: var(--ink); }
  .contact p { font-size: 17px; font-weight: 400; color: #2b2b2b; line-height: 24px; display: flex; align-items: center; gap: 6px; }
  .follow { left: 62px; }
  .visit { left: 425px; }
  .handle-dot { display: inline-block; width: 13px; height: 13px; border-radius: 50%; background: var(--ink-soft); }
  .handles span + .handle-dot { margin-left: 12px; }
  .divider { position: absolute; left: 414px; top: 702px; width: 1px; height: 46px; background: var(--ink-soft); }

  .location-pin { position: absolute; left: 985px; top: 505px; width: 160px; height: 240px; }
  .pin-label {
    position: absolute; left: 1022px; top: 560px; width: 86px; text-align: center; font-weight: 700;
    font-size: 16px; line-height: 18px; color: var(--ink);
  }
</style>
</head>
<body>
  <main class="flyer">
    <div class="sketch-area" role="img" aria-label="Faint architectural line sketch of tall buildings"></div>
    <div class="portrait-area" role="img" aria-label="Photo of a project manager in a suit and yellow hard hat seated on a white chair"></div>
    <div class="megaphone-area" role="img" aria-label="Silver megaphone illustration"></div>

    <div class="script-lead">We're</div>
    <h1 class="headline">HIRING</h1>

    <div class="role">
      <div class="role-top">CONSTRUCTION</div>
      <div class="role-bottom">PROJECT <strong>MANAGER</strong></div>
    </div>
    <div class="tag tag-build">BUILD <strong>LUXURY</strong></div>
    <div class="tag tag-lead">LEAD <strong>EXCELLENCE</strong></div>

    <section class="requirements">
      <div class="req-col req-col-left">
        <div class="req-item"><svg viewBox="0 0 12 12"><circle cx="6" cy="6" r="6" fill="#fff"/><path d="M3.2 6.2l1.8 1.8 3.8-3.8" stroke="#000" stroke-width="1.6" fill="none"/></svg>Experience <strong>5+ years</strong> in residential project management with a strong portfolio of completed homes.</div>
        <div class="req-item"><svg viewBox="0 0 12 12"><circle cx="6" cy="6" r="6" fill="#fff"/><path d="M3.2 6.2l1.8 1.8 3.8-3.8" stroke="#000" stroke-width="1.6" fill="none"/></svg>Excellent <strong>leadership skills</strong>, leads teams with confidence and clarity</div>
        <div class="req-item"><svg viewBox="0 0 12 12"><circle cx="6" cy="6" r="6" fill="#fff"/><path d="M3.2 6.2l1.8 1.8 3.8-3.8" stroke="#000" stroke-width="1.6" fill="none"/></svg><strong>Communicates seamlessly</strong> with architects , engineers, designers and clients</div>
      </div>
      <div class="req-col req-col-right">
        <div class="req-item"><svg viewBox="0 0 12 12"><circle cx="6" cy="6" r="6" fill="#fff"/><path d="M3.2 6.2l1.8 1.8 3.8-3.8" stroke="#333" stroke-width="1.6" fill="none"/></svg>Knows how to <strong>manage budgets and timelines</strong> without compromising quality</div>
        <div class="req-item"><svg viewBox="0 0 12 12"><circle cx="6" cy="6" r="6" fill="#fff"/><path d="M3.2 6.2l1.8 1.8 3.8-3.8" stroke="#333" stroke-width="1.6" fill="none"/></svg><strong>Solves problems</strong> with a positive solution first mindset</div>
        <div class="req-item"><svg viewBox="0 0 12 12"><circle cx="6" cy="6" r="6" fill="#fff"/><path d="M3.2 6.2l1.8 1.8 3.8-3.8" stroke="#333" stroke-width="1.6" fill="none"/></svg><strong>Pays attention to every detail</strong> because in luxury the small things are the big things</div>
      </div>
    </section>

    <div class="cta cta-link">Link in bio or DM to connect</div>
    <div class="cta cta-apply">Apply now</div>

    <div class="contact follow">
      <h3>Follow us</h3>
      <p class="handles"><span class="handle-dot"></span><span>velstridebuilders</span><span class="handle-dot"></span><span>VelstrideBldrs</span></p>
    </div>
    <div class="divider"></div>
    <div class="contact visit">
      <h3>Visit us</h3>
      <p>www.velstridebuilders.com</p>
    </div>

    <svg class="location-pin" viewBox="0 0 160 240" aria-hidden="true">
      <defs>
        <linearGradient id="pinFill" x1="0" y1="0" x2="1" y2="1">
          <stop offset="0" stop-color="#f2282c"/>
          <stop offset="1" stop-color="#b80f12"/>
        </linearGradient>
      </defs>
      <path d="M80 2C38 2 4 36 4 78c0 52 60 110 76 160 16-50 76-108 76-160C156 36 122 2 80 2z" fill="url(#pinFill)"/>
      <circle cx="81" cy="78" r="48" fill="#fff"/>
    </svg>
    <div class="pin-label">Bergen County, NJ</div>
  </main>
</body>
</html>
```